VKT Consulting

Government/Entitlement Consulting Services- I assist developers obtain entitlements from local, state and federal government agencies so that they can build their projects. Often these projects are very complicated and political and may face community opposition.

Target Market(s)

Real Estate Developers

Industry/Entity Type

Business Consultant

Contact Information for Business Card

Dana Melbrook
Principal

Font styles to use
Serif
Sans Serif

Requirements
Must have
• Classy and professional appeal.
Nice to have
• I like a combination of a mat and glossy finish. I've seen that done with black and then a bold color for a pop, but am not 100% committed to that.

```html
<!DOCTYPE html>
<html lang="en">
<head>
<meta charset="utf-8">
<title>VKT Consulting – Business Card</title>
<link rel="stylesheet" href="https://fonts.googleapis.com/css2?family=Open+Sans:wght@400;600;700&display=swap">
<style>
  :root {
    --page-bg: #e9e7e4;
    --card-bg: #1f2a35;
    --brand-blue: #4fd3f5;
    --text-light: #ffffff;
    --text-soft: #e8edf2;
  }
  * { margin: 0; padding: 0; box-sizing: border-box; }
  html, body {
    width: 1200px;
    height: 900px;
    overflow: hidden;
    background: var(--page-bg);
    font-family: "Open Sans", Arial, sans-serif;
  }
  .canvas { position: relative; width: 1200px; height: 900px; }

  .card {
    position: absolute;
    background: var(--card-bg);
    box-shadow: 0 6px 18px rgba(0,0,0,0.18);
  }
  .card--front { left: 238px; top: 62px; width: 555px; height: 342px; }
  .card--back  { left: 457px; top: 518px; width: 560px; height: 342px; }

  .brand-name {
    position: absolute;
    color: var(--brand-blue);
    font-weight: 700;
    white-space: nowrap;
    line-height: 1;
  }
  .card--front .brand-name { left: 68px; top: 158px; width: 188px; font-size: 24px; text-align: center; }
  .card--back .brand-name  { left: 0; right: 0; top: 156px; font-size: 27px; text-align: center; padding-left: 40px; }

  .contact {
    position: absolute;
    left: 291px;
    top: 86px;
    color: var(--text-soft);
    font-size: 14.5px;
    line-height: 20px;
  }
  .contact__name { font-size: 18px; font-weight: 600; color: var(--text-light); line-height: 24px; }
  .contact__title { margin-bottom: 14px; }
  .contact__address { margin-bottom: 14px; }
  .contact__row { display: flex; align-items: center; gap: 8px; }
  .contact__icon { width: 12px; height: 12px; fill: var(--text-soft); flex: none; }
</style>
</head>
<body>
<main class="canvas">
  <section class="card card--front">
    <div class="brand-name">VKT Consulting</div>
    <div class="contact">
      <div class="contact__name">Dana Melbrook</div>
      <div class="contact__title">Principal</div>
      <div class="contact__address">12345, Address Goes Here<br>Country Name, 123456.</div>
      <div class="contact__row">
        <svg class="contact__icon" viewBox="0 0 24 24"><path d="M6.6 10.8a15.1 15.1 0 0 0 6.6 6.6l2.2-2.2c.3-.3.7-.4 1-.2 1.1.4 2.3.6 3.6.6.6 0 1 .4 1 1V20c0 .6-.4 1-1 1C10.6 21 3 13.4 3 4c0-.6.4-1 1-1h3.5c.6 0 1 .4 1 1 0 1.3.2 2.5.6 3.6.1.3 0 .7-.2 1z"/></svg>
        <span>044-987 654 321</span>
      </div>
      <div class="contact__row">
        <svg class="contact__icon" viewBox="0 0 24 24"><path d="M2 5h20v14H2z M3 6l9 7 9-7" stroke="#1f2a35" stroke-width="1.6"/></svg>
        <span>info@vktmail.com</span>
      </div>
      <div class="contact__row">
        <svg class="contact__icon" viewBox="0 0 24 24"><circle cx="12" cy="12" r="10"/><path d="M12 2v20M2 12h20M6 5c3 3 9 3 12 0M6 19c3-3 9-3 12 0" stroke="#1f2a35" stroke-width="1.4" fill="none"/></svg>
        <span>www.vktconsulting.com</span>
      </div>
    </div>
  </section>

  <section class="card card--back">
    <div class="brand-name">VKT Consulting</div>
  </section>
</main>
</body>
</html>
```